Logo, Web and Mobile Designs for enterprise social media platform

All the details are in the attached document, please start reading the scope document first which explains what is this project about and the details about the needed deliverables, after that please read the UI_Requirements document which will detail what is expected regarding the coded web version since this is a coded contest, it is very important that you meet the UI requirements or suggest something else but we will need to agree first before working on the coded version

Good Luck

Target Market(s)

Enterprise Social Media

Industry/Entity Type

Media

Coding

Coded - Design and coding required

Number of Pages Required

5+ page

Font styles to use
Sans Serif

Requirements
Must have
• All the must haves are listed in the scope document so please check before you start

```html
<!DOCTYPE html>
<html lang="en">
<head>
<meta charset="utf-8">
<title>Teamora – About Us</title>
<link href="https://fonts.googleapis.com/css2?family=Ubuntu:wght@300;400;500&display=swap" rel="stylesheet">
<style>
:root{
  --blue:#1f8fc4;
  --blue-dark:#1d86b7;
  --orange:#f6a21b;
  --page:#ebebeb;
  --panel:#ffffff;
  --side:#f4f4f4;
  --line:#e3e3e3;
  --text:#555a60;
  --muted:#6b6f74;
  --header:#f8f8f8;
}
*{box-sizing:border-box;margin:0;padding:0}
html,body{width:1200px;height:1118px;overflow:hidden}
body{font-family:'Ubuntu',sans-serif;background:var(--page);position:relative;color:var(--text)}
.topbar{position:absolute;left:0;top:0;width:1200px;height:70px;background:var(--header);border-bottom:1px solid #dcdcdc}
.topbar .sep{position:absolute;top:0;width:1px;height:70px;background:#e2e2e2}
.menu-btn{position:absolute;left:101px;top:30px;width:18px}
.menu-btn span{display:block;height:3px;background:#777;margin-bottom:3px}
.brand{position:absolute;left:168px;top:18px;display:flex;align-items:center;gap:8px}
.brand-dot{width:34px;height:34px;border-radius:50%;background:var(--orange)}
.brand-name{font-size:30px;font-weight:500;color:var(--blue)}
.user{position:absolute;left:746px;top:19px;display:flex;align-items:center;gap:12px;font-size:17px;color:#555}
.avatar{width:34px;height:34px;border-radius:50%;background:#5c5c5c}
.caret{width:0;height:0;border-left:6px solid transparent;border-right:6px solid transparent;border-top:7px solid #555;margin-left:4px}
.icon{position:absolute;top:24px}
.badge{position:absolute;top:-8px;left:12px;min-width:20px;height:17px;border-radius:9px;color:#fff;font-size:11px;text-align:center;line-height:17px}
.badge.orange{background:var(--orange)}
.badge.blue{background:var(--blue)}
.panel{position:absolute;left:99px;top:105px;width:1001px;height:820px;background:var(--panel);border:1px solid #dadada}
.sidebar{position:absolute;left:0;top:0;width:278px;height:818px;background:var(--side);border-right:1px solid #dedede}
.side-top{height:56px;border-bottom:1px solid var(--line);display:flex;align-items:center;padding-left:17px;gap:14px;font-size:15px;color:#444}
.side-top svg{flex:none}
.side-nav{list-style:none;margin-top:20px}
.side-nav li{height:32.6px;border-bottom:1px solid var(--line);display:flex;align-items:center;padding-left:18px;font-size:16px;color:#555;font-weight:300}
.side-nav li::before{content:"";width:5px;height:5px;border-right:1.5px solid #666;border-top:1.5px solid #666;transform:rotate(45deg);margin-right:18px}
.side-nav li.active{color:var(--blue);font-weight:400;text-transform:uppercase}
.content{position:absolute;left:310px;top:0;width:660px}
.section-title{margin-top:38px;font-size:20px;font-weight:300;color:#555;letter-spacing:.3px;padding-bottom:14px;border-bottom:1px solid var(--line);position:relative}
.section-title::after{content:"";position:absolute;left:0;bottom:-1px;width:139px;height:1px;background:var(--blue)}
.company-title{margin-top:28px;font-size:20px;font-weight:400;color:var(--blue)}
.intro{display:flex;gap:29px;margin-top:17px}
.photo{flex:none;width:262px;height:178px;border:2px solid #e8e8e8;background:linear-gradient(160deg,#dfe9f6 0%,#7aa2d8 45%,#23569c 100%)}
.intro p{font-size:11.2px;line-height:20.6px;color:var(--text)}
.body-text{margin-top:14px;font-size:11.2px;line-height:20.6px;color:var(--text)}
.location{margin-top:44px;border:1px solid #e6e6e6;height:266px}
.location-head{height:49px;background:#f7f7f7;border-bottom:1px solid #e6e6e6;display:flex;align-items:center;padding-left:22px;gap:10px;font-size:15px;color:#444}
.map{height:215px;background:linear-gradient(135deg,#efe8d6 0%,#f1ecdf 50%,#e6e1d2 100%)}
.footer{position:absolute;left:0;top:970px;width:1200px;height:148px;background:var(--blue-dark);color:#fff;text-align:center}
.social{display:flex;justify-content:center;gap:13px;margin-top:29px}
.social span{width:24px;height:24px;border-radius:4px;background:#fff}
.foot-links{margin-top:17px;font-size:14px;font-weight:300}
.foot-links a{color:#fff;text-decoration:none}
.foot-links i{font-style:normal;margin:0 9px}
.copyright{margin-top:13px;font-size:14px}
</style>
</head>
<body>
<header class="topbar">
  <div class="sep" style="left:144px"></div>
  <div class="sep" style="left:922px"></div>
  <div class="sep" style="left:991px"></div>
  <div class="sep" style="left:1051px"></div>
  <div class="menu-btn"><span></span><span></span><span></span></div>
  <div class="brand"><div class="brand-dot"></div><div class="brand-name">Teamora</div></div>
  <div class="user"><div class="avatar"></div>Alex Carter<div class="caret"></div></div>
  <div class="icon" style="left:946px">
    <svg width="20" height="20" viewBox="0 0 20 20"><rect x="0" y="1" width="20" height="4" fill="#666"/><rect x="0" y="8" width="20" height="4" fill="#666"/><rect x="0" y="15" width="12" height="4" fill="#666"/></svg>
    <span class="badge orange">8</span>
  </div>
  <div class="icon" style="left:1011px">
    <svg width="20" height="20" viewBox="0 0 20 20"><circle cx="8" cy="8" r="6" fill="none" stroke="#666" stroke-width="2.6"/><line x1="12.5" y1="12.5" x2="18" y2="18" stroke="#666" stroke-width="3" stroke-linecap="round"/></svg>
  </div>
  <div class="icon" style="left:1072px">
    <svg width="20" height="22" viewBox="0 0 20 22"><path d="M10 1c-4 0-6 3-6 7v5l-3 4h18l-3-4V8c0-4-2-7-6-7z" fill="#666"/><circle cx="10" cy="19.5" r="2.3" fill="#666"/></svg>
    <span class="badge blue">8</span>
  </div>
</header>

<main class="panel">
  <aside class="sidebar">
    <div class="side-top">
      <svg width="15" height="13" viewBox="0 0 15 13"><rect x="0" y="0" width="7" height="6" fill="var(--blue)"/><rect x="8" y="0" width="7" height="6" fill="var(--blue)"/><rect x="0" y="7" width="7" height="6" fill="var(--blue)"/><rect x="8" y="7" width="7" height="6" fill="var(--blue)"/></svg>
      VIEW DASHBOARD
    </div>
    <div class="side-top">
      <svg width="15" height="15" viewBox="0 0 15 15"><rect x="0.5" y="2" width="14" height="12.5" fill="none" stroke="var(--blue)" stroke-width="1.4"/><rect x="0" y="2" width="15" height="3" fill="var(--blue)"/><g fill="var(--blue)"><rect x="3" y="7" width="2" height="2"/><rect x="6.5" y="7" width="2" height="2"/><rect x="10" y="7" width="2" height="2"/><rect x="3" y="10.5" width="2" height="2"/><rect x="6.5" y="10.5" width="2" height="2"/><rect x="10" y="10.5" width="2" height="2"/></g></svg>
      VIEW EVENT
    </div>
    <ul class="side-nav">
      <li class="active">About Us</li>
      <li>Speakers</li>
      <li>Track</li>
      <li>Sessions</li>
      <li>Tickets</li>
      <li>Organizers</li>
      <li>Sponsors</li>
      <li>Exhibitor</li>
      <li>Security</li>
      <li>Members</li>
    </ul>
  </aside>

  <section class="content">
    <h1 class="section-title">DESCRIPTION</h1>
    <h2 class="company-title">ABOUT OUR COMPANY</h2>
    <div class="intro">
      <div class="photo" role="img" aria-label="Upward view of a blue glass office tower"></div>
      <p>Sed ut perspiciatis unde omnis iste natus error sit voluptatem accusantium doloremque laudantium, totam rem aperiam, eaque ipsa quae ab illo inventore veritatis et quasi architecto beatae vitae dicta sunt explicabo. Nemo enim ipsam voluptatem quia voluptas sit aspernatur aut odit aut fugit, sed quia consequuntur magni dolores eos qui ratione voluptatem sequi nesciunt. Neque porro quisquam est, qui dolorem ipsum quia dolor sit amet, consectetur, adipisci velit, sed quia non numquam eius modi tempora incidunt ut labore et dolore magnam aliquam quaerat voluptatem.</p>
    </div>
    <p class="body-text">Sed ut perspiciatis unde omnis iste natus error sit voluptatem accusantium doloremque laudantium, totam rem aperiam, eaque ipsa quae ab illo inventore veritatis et quasi architecto beatae vitae dicta sunt explicabo. Nemo enim ipsam voluptatem quia voluptas sit aspernatur aut odit aut fugit, sed quia consequuntur magni dolores eos qui ratione voluptatem sequi nesciunt. Neque porro quisquam est, qui dolorem ipsum quia dolor sit amet, consectetur, adipisci velit, sed quia non numquam eius modi tempora incidunt ut labore et dolore magnam aliquam quaerat voluptatem.</p>
    <div class="location">
      <div class="location-head">
        <svg width="10" height="14" viewBox="0 0 10 14"><path d="M5 0a5 5 0 0 0-5 5c0 4 5 9 5 9s5-5 5-9a5 5 0 0 0-5-5z" fill="#555"/><circle cx="5" cy="5" r="2" fill="#f7f7f7"/></svg>
        LOCATION INFORMATION
      </div>
      <div class="map" role="img" aria-label="Street map showing the company location"></div>
    </div>
  </section>
</main>

<footer class="footer">
  <div class="social"><span></span><span></span><span></span><span></span><span></span></div>
  <nav class="foot-links"><a href="#">Home</a><i>/</i><a href="#">Contact</a><i>/</i><a href="#">Topics</a><i>/</i><a href="#">Posts and Comments</a><i>/</i><a href="#">Discussion</a><i>/</i><a href="#">Videos Links</a></nav>
  <p class="copyright">Copyright @ 2015 - 2015.Teamora. All Rights Reserved.</p>
</footer>
</body>
</html>
```